Rack Card for Bright Meadow Dog Training

I love the logo you designed for me a while back (I had it updated and have the new files).

I need a rack card designed, 2 sided.

One side will be Bright Meadow Dog Training (my general dog training business)

The other side will be my Deaf and Blind Dog Training Business speciality.

Both sides Full Color/4 color

3.5 x 8.5 inches

I can provide photos and text accordingly.

Let me know the estimated price and Turn around time.

```html
<!DOCTYPE html>
<html lang="en">
<head>
<meta charset="utf-8">
<title>Bright Meadow Dog Training – Rack Cards</title>
<link rel="stylesheet" href="https://fonts.googleapis.com/css2?family=Montserrat:wght@400;500;600;700;800&family=Playball&display=swap">
<style>
  :root{
    --ink:#3a3a36;
    --ink-deep:#2f2f2c;
    --cream:#e9e4d6;
    --paper:#ffffff;
    --orange:#f39a12;
    --photo-warm:#a9784f;
    --photo-cool:#9aa3a1;
    --photo-green:#8b9c6a;
    --page:#f4f4f4;
  }
  *{box-sizing:border-box;margin:0;padding:0}
  html,body{width:1200px;height:2557px;overflow:hidden}
  body{background:var(--page);font-family:"Montserrat",sans-serif;color:var(--ink);position:relative}
  .rack-card{position:absolute;top:637px;width:528px;height:1282px;overflow:hidden;background:var(--paper);box-shadow:0 6px 18px rgba(0,0,0,.12)}
  .rack-card--general{left:63px}
  .rack-card--specialty{left:630px}
  .card-shapes{position:absolute;inset:0}
  .abs{position:absolute}

  .logo-badge{position:absolute;width:190px;height:190px;border-radius:50%;background:var(--paper);border:6px solid var(--ink);display:flex;align-items:center;justify-content:center;text-align:center}
  .logo-badge__name{font-weight:600;font-size:22px;line-height:1.15;color:var(--ink)}

  .photo{position:absolute;background:linear-gradient(160deg,var(--photo-cool),var(--photo-warm))}
  .photo--round{border-radius:50%;border:4px solid var(--paper);box-shadow:0 0 0 3px var(--ink)}

  .script-name{font-family:"Playball",cursive;color:var(--orange);font-size:46px;line-height:1}
  .hero-title{font-weight:800;color:var(--paper);line-height:.95;letter-spacing:-1px}
  .spec-title{font-weight:800;color:var(--ink);font-size:49px;line-height:.95;letter-spacing:-.5px}

  .pill{position:absolute;background:var(--ink);color:var(--paper);border-radius:14px;font-weight:800;display:flex;align-items:center;justify-content:center;white-space:nowrap}
  .pill em{font-style:normal;color:var(--orange)}

  .areas{font-weight:700;font-size:14.5px;line-height:1.25;color:var(--ink)}
  .service-label{position:absolute;top:737px;text-align:center;font-weight:800;font-size:16.5px;line-height:1.1;color:var(--ink)}

  .teach-list{position:absolute;left:36px;top:848px;width:470px;list-style:none}
  .teach-list li{display:flex;gap:12px;font-size:12.6px;line-height:1.35;color:var(--ink);margin-bottom:13px}
  .teach-list svg{flex:none;width:22px;height:20px;margin-top:2px}
  .teach-list b{font-weight:700}

  .body-copy{position:absolute;font-size:12.8px;line-height:1.3;color:var(--ink)}

  .trainer-name{font-weight:800;color:var(--orange);font-size:19px}
  .trainer-role{font-weight:500;color:var(--paper);font-size:15px;letter-spacing:6px;margin-top:4px}

  .consult{position:absolute;left:0;width:528px;top:1155px;text-align:center;font-weight:700;font-size:12.5px;color:var(--ink)}
  .consult em{font-style:normal;color:var(--orange)}
  .phones{position:absolute;top:1188px;left:0;width:528px;display:flex;justify-content:center;gap:16px;align-items:center}
  .phone-group{display:flex;align-items:center;gap:6px}
  .phone-region{font-size:11px;font-weight:500;line-height:1.05;color:var(--ink)}
  .phone-number{display:flex;align-items:center;gap:4px;background:var(--ink);color:var(--paper);font-weight:600;font-size:14px;border-radius:10px;padding:3px 9px 3px 5px}
  .phone-number svg{width:14px;height:14px}
  .site-url{position:absolute;left:0;width:528px;top:1230px;height:52px;display:flex;align-items:center;justify-content:center;color:var(--paper);font-size:21px;font-weight:500}
</style>
</head>
<body>

<!-- GENERAL TRAINING SIDE -->
<section class="rack-card rack-card--general">
  <svg class="card-shapes" viewBox="0 0 528 1282" aria-hidden="true">
    <rect width="528" height="180" fill="var(--cream)"/>
    <path d="M0 150 C120 70 300 190 528 110 L528 400 C400 440 200 380 0 420 Z" fill="var(--ink)"/>
    <path d="M0 420 C200 380 400 440 528 400 L528 432 C380 470 200 410 0 448 Z" fill="var(--cream)"/>
    <path d="M5 428 C120 446 200 408 280 440 S430 398 495 428" fill="none" stroke="var(--ink)" stroke-width="1.5" stroke-dasharray="3 6"/>
    <circle cx="495" cy="428" r="4" fill="var(--ink)"/>
    <path d="M0 625 C150 598 380 640 528 612 L528 730 L0 730 Z" fill="var(--ink)"/>
    <rect x="17" y="712" width="117" height="60" rx="14" fill="var(--paper)"/>
    <rect x="138" y="712" width="118" height="60" rx="14" fill="var(--paper)"/>
    <rect x="261" y="712" width="108" height="60" rx="14" fill="var(--paper)"/>
    <rect x="375" y="712" width="130" height="60" rx="14" fill="var(--paper)"/>
    <path d="M0 1135 C150 1105 380 1152 528 1120 L528 1282 L0 1282 Z" fill="var(--cream)"/>
    <rect y="1230" width="528" height="52" fill="var(--ink)"/>
  </svg>

  <div class="photo" style="left:238px;top:0;width:290px;height:390px;background:radial-gradient(ellipse at 55% 45%,#6b5440,#3a3a36 70%);" role="img" aria-label="Photo of a black and tan dog leaping toward the camera"></div>

  <div class="logo-badge" style="left:42px;top:10px;"><span class="logo-badge__name">Bright<br>Meadow</span></div>

  <div class="abs script-name" style="left:38px;top:212px;">Bright Meadow</div>
  <div class="abs hero-title" style="left:38px;top:262px;font-size:76px;">DOG</div>
  <div class="abs hero-title" style="left:38px;top:330px;font-size:57px;">TRAINING</div>

  <div class="pill" style="left:40px;top:483px;width:400px;height:37px;font-size:16.5px;"><em>BRIGHT MEADOW DOG TRAINING</em>&nbsp;SERVICES</div>

  <p class="abs areas" style="left:39px;top:537px;width:460px;">DOG TRAINING IN REDONDO BEACH, MANHATTAN BEACH, SOUTH BAY, LONG BEACH, AND THE WEST SIDE</p>

  <div class="photo photo--round" style="left:37px;top:590px;width:104px;height:104px;background:linear-gradient(180deg,#c6d7a3,var(--photo-green));" role="img" aria-label="Photo of a young puppy standing on grass"></div>
  <div class="photo photo--round" style="left:150px;top:590px;width:104px;height:104px;background:linear-gradient(160deg,#8a5430,#5c3a22);" role="img" aria-label="Photo of an adult brown dog"></div>
  <div class="photo photo--round" style="left:263px;top:590px;width:104px;height:104px;background:linear-gradient(180deg,#b9cad6,#8a6a4a);" role="img" aria-label="Photo of a happy rescue dog"></div>
  <div class="photo photo--round" style="left:377px;top:590px;width:104px;height:104px;background:linear-gradient(160deg,#a0512a,#d8d2c8);" role="img" aria-label="Photo of a dog among torn stuffing"></div>

  <div class="service-label" style="left:17px;width:117px;">PUPPY<br>TRAINING</div>
  <div class="service-label" style="left:138px;width:118px;">ADULT DOG<br>TRAINING</div>
  <div class="service-label" style="left:261px;width:108px;">RESCUE<br>DOGS</div>
  <div class="service-label" style="left:375px;width:130px;">BEHAVIORAL<br>ISSUES</div>

  <div class="pill" style="left:37px;top:790px;width:293px;height:36px;font-size:17px;"><em>WE TEACH</em>&nbsp;OWNERS HOW TO</div>

  <ul class="teach-list">
    <li><svg viewBox="0 0 22 20"><use href="#paw"/></svg><span><b>We teach dogs of all ages:</b> Puppies, Adolescents &amp; Adults.</span></li>
    <li><svg viewBox="0 0 22 20"><use href="#paw"/></svg><span>Become the “Pack Guardian”.<br>Read your dog’s signals (body language, signs of anxiety, etc.) and how to motivate him.</span></li>
    <li><svg viewBox="0 0 22 20"><use href="#paw"/></svg><span>Use structured play and games to obtain desired behavior and have fun with your dog.</span></li>
    <li><svg viewBox="0 0 22 20"><use href="#paw"/></svg><span>Good manners – what all good dogs should know.</span></li>
    <li><svg viewBox="0 0 22 20"><use href="#paw"/></svg><span>Proper leash and obedience skills (no pulling<br>or lunging).</span></li>
    <li><svg viewBox="0 0 22 20"><use href="#paw"/></svg><span>How to handle ‘real-world experiences’ (skateboards, loud noises, meet and greet new people and dogs, etc.).</span></li>
  </ul>

  <p class="consult">SCHEDULE <em>FREE</em> 15 MINUTE PHONE CONSULTATIONA</p>
  <div class="phones">
    <div class="phone-group"><span class="phone-region">LOS<br>ANGELES</span><span class="phone-number"><svg viewBox="0 0 16 16"><use href="#phone"/></svg>(310) 555-0142</span></div>
    <div class="phone-group"><span class="phone-region">ORANGE<br>COUNTY</span><span class="phone-number"><svg viewBox="0 0 16 16"><use href="#phone"/></svg>(714) 555-0187</span></div>
  </div>
  <div class="site-url">brightmeadowdogtraining.com</div>
</section>

<!-- DEAF & BLIND SPECIALTY SIDE -->
<section class="rack-card rack-card--specialty">
  <svg class="card-shapes" viewBox="0 0 528 1282" aria-hidden="true">
    <rect width="528" height="430" fill="var(--ink)"/>
    <path d="M0 0 L528 0 L528 60 L330 60 C260 80 180 140 0 120 Z" fill="var(--ink)"/>
    <path d="M215 130 C300 150 330 70 528 70 L528 400 C400 420 200 390 0 412 L0 380 C80 370 170 330 215 130 Z" fill="var(--cream)"/>
    <path d="M0 412 C200 390 400 420 528 400 L528 430 C380 440 200 420 0 440 Z" fill="var(--paper)"/>
    <path d="M460 410 C490 405 510 410 522 414" fill="none" stroke="var(--ink)" stroke-width="1.5" stroke-dasharray="3 6"/>
    <circle cx="522" cy="414" r="3.5" fill="var(--ink)"/>
    <path d="M5 627 C20 615 35 612 45 614" fill="none" stroke="var(--ink)" stroke-width="1.5" stroke-dasharray="3 6"/>
    <circle cx="5" cy="627" r="3.5" fill="var(--ink)"/>
    <path d="M258 778 C330 755 370 765 400 790" fill="none" stroke="var(--ink)" stroke-width="1.5" stroke-dasharray="3 6"/>
    <circle cx="258" cy="778" r="3.5" fill="var(--ink)"/>
    <path d="M0 1000 C120 960 250 1005 528 980 L528 1120 L0 1120 Z" fill="var(--ink)"/>
    <path d="M0 1135 C150 1105 380 1152 528 1120 L528 1282 L0 1282 Z" fill="var(--cream)"/>
    <rect y="1230" width="528" height="52" fill="var(--ink)"/>
    <path d="M488 436 A86 86 0 0 1 430 585" fill="none" stroke="var(--ink)" stroke-width="7"/>
    <path d="M46 654 A86 86 0 0 1 180 596" fill="none" stroke="var(--ink)" stroke-width="7"/>
    <path d="M470 945 A86 86 0 0 1 330 960" fill="none" stroke="var(--ink)" stroke-width="7"/>
  </svg>

  <div class="photo" style="left:0;top:55px;width:215px;height:325px;background:radial-gradient(ellipse at 50% 50%,#5a5a55,#2f2f2c 70%);" role="img" aria-label="Photo of a black and white dog raising its paw"></div>

  <div class="logo-badge" style="left:282px;top:20px;"><span class="logo-badge__name">Bright<br>Meadow</span></div>

  <div class="abs spec-title" style="left:198px;top:215px;">DEAF &amp;<br>BLIND DOG<br>TRAINING</div>

  <div class="pill" style="left:37px;top:423px;width:226px;height:30px;font-size:17px;"><em>DEAF DOG</em>&nbsp;TRAINING</div>
  <p class="body-copy" style="left:40px;top:462px;width:275px;">Deaf dogs can easily be trained using hand signals. We owe it to our dogs to teach them how to behave, and that the world is a safe place.A dog with special needs is no exception.Training a dog that is deaf can come with it challenges.</p>
  <div class="photo photo--round" style="left:326px;top:418px;width:166px;height:166px;background:linear-gradient(160deg,#c9d4dc,#7a5434);" role="img" aria-label="Photo of a brown and white dog"></div>

  <div class="photo photo--round" style="left:38px;top:603px;width:166px;height:166px;background:linear-gradient(160deg,#b47a4e,#7a4a2a);" role="img" aria-label="Photo of an older golden dog"></div>
  <div class="pill" style="left:213px;top:610px;width:254px;height:31px;font-size:17px;"><em>BLIND DOG</em>&nbsp;TRAINING</div>
  <p class="body-copy" style="left:214px;top:650px;width:290px;">Deaf dogs can easily be trained using sound signals.We owe it to our dogs to teach them how to behave, to know their surrounding even with their sight is loss, and that the world is a safe place.</p>

  <div class="pill" style="left:37px;top:788px;width:306px;height:31px;font-size:17px;"><em>DEAF / BLIND</em>&nbsp;DOG TRAINING</div>
  <p class="body-copy" style="left:40px;top:828px;width:265px;">Deaf dogs can easily be trained using sound signals. We owe it to our dogs to teach them how to behave, to know their surrounding even with their sight is loss, and that the world is a safe place.</p>
  <div class="photo photo--round" style="left:322px;top:802px;width:166px;height:166px;background:linear-gradient(160deg,#7f9a5a,#e6e2da);" role="img" aria-label="Photo of a white service dog wearing a vest beside a tree"></div>

  <div class="photo photo--round" style="left:43px;top:938px;width:184px;height:184px;background:linear-gradient(160deg,#d8cdbd,#b07a44);" role="img" aria-label="Photo of the lead trainer hugging several dogs"></div>
  <div class="abs" style="left:243px;top:1045px;">
    <div class="trainer-name">DANA WHITFIELD</div>
    <div class="trainer-role">LEAD TRAINER</div>
  </div>

  <p class="consult">SCHEDULE <em>FREE</em> 15 MINUTE PHONE CONSULTATIONA</p>
  <div class="phones">
    <div class="phone-group"><span class="phone-region">LOS<br>ANGELES</span><span class="phone-number"><svg viewBox="0 0 16 16"><use href="#phone"/></svg>(310) 555-0142</span></div>
    <div class="phone-group"><span class="phone-region">ORANGE<br>COUNTY</span><span class="phone-number"><svg viewBox="0 0 16 16"><use href="#phone"/></svg>(714) 555-0187</span></div>
  </div>
  <div class="site-url">brightmeadowdogtraining.com</div>
</section>

<svg width="0" height="0" style="position:absolute" aria-hidden="true">
  <defs>
    <g id="paw" fill="var(--ink)">
      <ellipse cx="5" cy="7" rx="2.3" ry="3"/>
      <ellipse cx="9.5" cy="4" rx="2.3" ry="3"/>
      <ellipse cx="14.5" cy="4" rx="2.3" ry="3"/>
      <ellipse cx="19" cy="7" rx="2.3" ry="3"/>
      <path d="M12 9 C16 9 18 14 17 16 C16 18 13 17 12 17 C11 17 8 18 7 16 C6 14 8 9 12 9 Z"/>
    </g>
    <g id="phone">
      <circle cx="8" cy="8" r="8" fill="var(--orange)"/>
      <path d="M5.2 4 L6.7 4 L7.4 6 L6.5 6.8 C7 8 8 9 9.2 9.5 L10 8.6 L12 9.3 L12 10.8 C12 11.4 11.5 12 10.8 12 C7.3 11.8 4.2 8.7 4 5.2 C4 4.5 4.6 4 5.2 4 Z" fill="var(--paper)"/>
    </g>
  </defs>
</svg>

</body>
</html>
```